New Business Card Design Project

I'd like a business card design around the same modern style that I used on my website www.brovanhs.com
It's gonna be one of those round corners double-sided business cards with maybe a big logo on the front and all the info on the back of the card.

Contact Information for Business Card

Marco Delgado
425-317-6084
www.brovanhs.com

www.facebook.com/BrovanHomeServices
www.intsgram.com/BrovanHomeServices

Requirements
Must have
• it needs to look elegant and modern

```html
<!DOCTYPE html>
<html lang="en">
<head>
<meta charset="utf-8">
<title>Brovan Home Services – Business Card</title>
<link rel="stylesheet" href="https://fonts.googleapis.com/css2?family=Montserrat:wght@500;600;800&display=swap">
<style>
  :root{
    --stage:#e9eaec;
    --card:#ffffff;
    --ink:#1f1d1e;
    --brand:#1ba3e8;
    --light:#ffffff;
  }
  *{box-sizing:border-box;margin:0;padding:0}
  html,body{width:1200px;height:800px;overflow:hidden}
  body{background:var(--stage);font-family:"Montserrat",sans-serif;position:relative}
  .card{position:absolute;left:330px;width:540px;height:309px;background:var(--card);
        box-shadow:0 6px 20px rgba(0,0,0,.15);overflow:hidden}
  .card--front{top:50px}
  .card--back{top:420px}
  .brand{position:absolute;display:flex;align-items:center;gap:12px;color:var(--brand);font-weight:800}
  .brand__dot{width:18px;height:18px;border-radius:50%;background:var(--brand);flex:none}
  .brand__text{display:flex;flex-direction:column;line-height:1}
  .brand__name{font-size:58px;letter-spacing:-1px}
  .brand__tag{font-size:15px;letter-spacing:2px;text-transform:uppercase;margin-top:4px}
  .card--front .brand{left:50%;top:50%;transform:translate(-50%,-50%)}
  .card--back .brand{left:262px;top:40px}
  .card--back .brand__name{font-size:48px}
  .card--back .brand__tag{font-size:13px}
  .sparkle-area{position:absolute;left:14px;top:150px;width:110px;height:110px;border-radius:50%;
        background:radial-gradient(circle,rgba(27,163,232,.55),rgba(27,163,232,0) 70%)}
  .back-band{position:absolute;inset:0}
  .contact{position:absolute;color:var(--light);font-size:11.5px;font-weight:500}
  .contact__row{display:flex;align-items:center;gap:7px;margin-top:5px}
  .contact__name{font-size:17px;font-weight:600;margin-bottom:4px}
  .icon{width:14px;height:14px;background:var(--brand);border-radius:2px;display:flex;align-items:center;justify-content:center;flex:none}
  .icon svg{width:10px;height:10px}
  .contact--person{left:206px;top:228px}
  .contact--social{left:352px;top:222px}
</style>
</head>
<body>
  <section class="card card--front">
    <div class="brand">
      <span class="brand__dot"></span>
      <div class="brand__text"><span class="brand__name">Brovan</span><span class="brand__tag">Home Services</span></div>
    </div>
  </section>

  <section class="card card--back">
    <svg class="back-band" viewBox="0 0 540 309" width="540" height="309">
      <polyline points="140,309 182,206 300,186 345,196 540,96" fill="none" stroke="var(--ink)" stroke-width="4"/>
      <polygon points="155,309 194,214 302,196 346,208 540,110 540,309" fill="var(--ink)"/>
    </svg>
    <div class="sparkle-area" role="img" aria-label="Blue sparkle decoration"></div>
    <div class="brand">
      <span class="brand__dot"></span>
      <div class="brand__text"><span class="brand__name">Brovan</span><span class="brand__tag">Home Services</span></div>
    </div>
    <div class="contact contact--person">
      <p class="contact__name">Marco Delgado</p>
      <p class="contact__row"><span class="icon"><svg viewBox="0 0 24 24"><path fill="#fff" d="M6.6 10.8a15 15 0 0 0 6.6 6.6l2.2-2.2a1 1 0 0 1 1-.25 11.4 11.4 0 0 0 3.6.57 1 1 0 0 1 1 1V20a1 1 0 0 1-1 1A17 17 0 0 1 3 4a1 1 0 0 1 1-1h3.5a1 1 0 0 1 1 1c0 1.25.2 2.45.57 3.57a1 1 0 0 1-.25 1z"/></svg></span>425-317-6084</p>
      <p class="contact__row"><span class="icon"><svg viewBox="0 0 24 24"><circle cx="12" cy="12" r="9" fill="none" stroke="#fff" stroke-width="2"/><path d="M3 12h18M12 3c3 3 3 15 0 18M12 3c-3 3-3 15 0 18" fill="none" stroke="#fff" stroke-width="1.6"/></svg></span>www.brovanhs.com</p>
    </div>
    <div class="contact contact--social">
      <p class="contact__row"><span class="icon"></span>BrovanHomeServices</p>
      <p class="contact__row"><span class="icon"></span>BrovanHomeServices</p>
    </div>
  </section>
</body>
</html>
```